Business card for a Exhibition booth fabrication company

Hi. My company would like to change our corporate name card. We are an events and Exhibition stand builder company. We would like our corporate name card to resonate what we do. I need someone to create something unique that relates to the industry that I am in. The graphic designer should be creative to incorporate the elements of my industry and try to blend in well in the design of the card. Our aim is to ensure that we are unique and our card can look different from our competitors.
Updates

Target Market(s)

Marketing and events manager from all companies

Contact Information for Business Card

The business card should have the following details:
Name
Job Title
Email
Website

Colors

Designer to choose colors to be used in the design.

Requirements
Must have
• The card must be look something that is relevant to the service that I am providing. My website is: www.velmora-buildworks.com
• You can see my website to get more information on what service that I am doing
Nice to have
• On the back of my card, I would like to have a globe image with the incorporation of my company logo. This is to indicate that my services can be done in any part of the world.

```html
<!DOCTYPE html>
<html lang="en">
<head>
<meta charset="utf-8">
<title>Velmora Buildworks – Business Card</title>
<link rel="stylesheet" href="https://fonts.googleapis.com/css2?family=Montserrat:wght@600&family=Roboto+Condensed:wght@700&family=Open+Sans:wght@400&family=Tinos&display=swap">
<style>
  :root {
    --bg: #e6e7ea;
    --card: #ffffff;
    --red: #e21d28;
    --black: #111113;
    --ink: #3a3a3c;
    --grey: #5d5b5c;
    --map-light: #ececec;
    --map-dark: #cfcfcf;
  }
  * { margin: 0; padding: 0; box-sizing: border-box; }
  html, body { width: 1200px; height: 1200px; overflow: hidden; background: var(--bg); }
  .sheet {
    width: 1200px; height: 1200px;
    display: flex; flex-direction: column; align-items: center; justify-content: center; gap: 60px;
  }
  .card {
    position: relative; width: 900px; height: 520px;
    background: var(--card); overflow: hidden;
    box-shadow: 0 6px 18px rgba(0,0,0,.18);
  }
  .card svg.art { position: absolute; inset: 0; }

  /* front */
  .brand {
    position: absolute; display: flex; align-items: center; gap: 10px;
    font-family: "Montserrat", sans-serif; font-weight: 600; color: var(--ink);
    letter-spacing: .14em; text-transform: uppercase; white-space: nowrap;
  }
  .front .brand { left: 180px; top: 80px; font-size: 17px; }
  .brand-mark { width: 14px; height: 14px; background: var(--red); flex: none; }
  .holder { position: absolute; left: 60px; top: 180px; }
  .holder-name {
    font-family: "Roboto Condensed", sans-serif; font-weight: 700; font-size: 44px; line-height: 1;
  }
  .holder-name .first { color: var(--red); }
  .holder-name .last { color: var(--grey); }
  .holder-title { font-family: "Tinos", serif; font-size: 24px; color: var(--ink); margin-top: 4px; }
  .contacts {
    position: absolute; left: 46px; top: 282px; list-style: none;
    font-family: "Open Sans", sans-serif; font-size: 21px; color: #fff;
  }
  .contacts li { display: flex; align-items: center; gap: 12px; height: 34px; white-space: nowrap; }
  .contacts svg { width: 22px; height: 22px; flex: none; }

  /* back */
  .world-map {
    position: absolute; left: 200px; top: 40px; width: 600px; height: 360px;
    border-radius: 40px;
    background: radial-gradient(ellipse at 50% 45%, var(--map-dark), var(--map-light) 70%, rgba(236,236,236,0) 100%);
    opacity: .8;
  }
  .back .brand {
    left: 0; right: 0; top: 250px; justify-content: center; font-size: 34px; gap: 16px;
  }
  .back .brand-mark { width: 24px; height: 24px; }
</style>
</head>
<body>
<main class="sheet">

  <section class="card front" aria-label="Business card front">
    <svg class="art" viewBox="0 0 900 520" width="900" height="520" aria-hidden="true">
      <rect class="contact-band" x="0" y="262" width="620" height="110" fill="var(--black)"/>
      <rect class="accent-rule" x="0" y="384" width="620" height="8" fill="var(--red)"/>
      <polygon class="corner-block" points="900,300 900,520 560,520" fill="var(--red)"/>
    </svg>

    <div class="brand"><span class="brand-mark"></span>Velmora Buildworks</div>

    <div class="holder">
      <p class="holder-name"><span class="first">Alan</span> <span class="last">Marsh</span></p>
      <p class="holder-title">Director</p>
    </div>

    <ul class="contacts">
      <li>
        <svg viewBox="0 0 24 24"><rect x="2" y="5" width="20" height="14" fill="var(--red)"/><path d="M3 6l9 7 9-7" fill="none" stroke="#fff" stroke-width="1.6"/></svg>
        username@velmora-buildworks.com
      </li>
      <li>
        <svg viewBox="0 0 24 24"><circle cx="12" cy="12" r="10" fill="var(--red)"/><g fill="none" stroke="#fff" stroke-width="1.2"><ellipse cx="12" cy="12" rx="4.5" ry="10"/><path d="M2 12h20M4 7h16M4 17h16M12 2v20"/></g></svg>
        www.velmora-buildworks.com
      </li>
    </ul>
  </section>

  <section class="card back" aria-label="Business card back">
    <div class="world-map" role="img" aria-label="Faint grey world map showing the continents"></div>
    <div class="brand"><span class="brand-mark"></span>Velmora Buildworks</div>
  </section>

</main>
</body>
</html>
```